New Innovative Counselling and psychotherapy Service needs Business Card design

Keep it simple and professional. On one side, just company name and logo (perhaps in all blue) and maybe a tag line.

On other side (all white) my name and Qualifications in centre

Industry/Entity Type

Health And Wellness

Contact Information for Business Card

Dara Whelby
Counsellor & Psychotherapist
BSc (Psychol.), BA, Dip. (Couns. & Psych.), PG.Cert (CBT), FGTrK, ONRE

I will also require Mobile no, Email and web site address of which I'll pass on to final designer.

Font styles to use
Sans Serif

Requirements
Must have
• My Logo Only and please use the colours in logo that is in it.
Should not have
• Any other images

```html
<!DOCTYPE html>
<html lang="en">
<head>
<meta charset="utf-8">
<title>Willow Crest – Business Card</title>
<link href="https://fonts.googleapis.com/css2?family=Open+Sans:wght@300;400;600;700&display=swap" rel="stylesheet">
<style>
  :root {
    --stage: #2b2b2b;
    --card: #ffffff;
    --brand-blue: #45b3ea;
    --brand-green: #8dc84f;
    --ink: #3a3a3a;
    --muted: #9a9a9a;
  }
  * { margin: 0; padding: 0; box-sizing: border-box; }
  html, body { width: 1200px; height: 900px; overflow: hidden; }
  body {
    background: var(--stage);
    font-family: "Open Sans", Arial, sans-serif;
    position: relative;
  }
  .card {
    position: absolute;
    left: 250px;
    width: 700px;
    height: 400px;
    background: var(--card);
    overflow: hidden;
  }
  .card--front { top: 35px; }
  .card--back { top: 465px; }

  /* Front */
  .brand {
    position: absolute;
    top: 70px;
    right: 80px;
    display: flex;
    align-items: center;
    gap: 16px;
  }
  .brand__dot {
    width: 46px; height: 46px;
    border-radius: 50%;
    background: var(--brand-blue);
  }
  .brand__name {
    font-weight: 300;
    font-size: 44px;
    color: var(--ink);
    letter-spacing: 0.5px;
  }
  .tagline {
    position: absolute;
    left: 60px;
    bottom: 60px;
    font-weight: 300;
    font-size: 19px;
    line-height: 1.35;
    color: var(--muted);
  }

  /* Back */
  .emblem {
    position: absolute;
    right: 55px;
    top: 70px;
    width: 260px;
    height: 260px;
    border-radius: 50%;
    background: var(--brand-blue);
  }
  .details {
    position: absolute;
    left: 55px;
    top: 62px;
    width: 330px;
  }
  .details__rule {
    height: 4px;
    width: 270px;
    background: var(--brand-blue);
    margin-bottom: 22px;
  }
  .details__name {
    font-weight: 700;
    font-size: 22px;
    color: var(--brand-blue);
    text-transform: uppercase;
    letter-spacing: 0.5px;
  }
  .details__role {
    font-weight: 400;
    font-size: 19px;
    color: var(--brand-green);
    text-transform: uppercase;
    margin-top: 2px;
  }
  .details__quals {
    font-size: 12.5px;
    color: var(--brand-green);
    line-height: 1.4;
    margin-top: 4px;
  }
  .contact {
    list-style: none;
    margin-top: 26px;
    font-size: 17px;
    color: var(--ink);
    line-height: 1.45;
  }
  .contact__label {
    color: var(--brand-blue);
    font-weight: 700;
  }
</style>
</head>
<body>
  <section class="card card--front">
    <div class="brand">
      <span class="brand__dot"></span>
      <span class="brand__name">Willow Crest</span>
    </div>
    <p class="tagline">Caring For Your Psychological<br>Well Being Is Our Top Priority</p>
  </section>

  <section class="card card--back">
    <div class="emblem"></div>
    <div class="details">
      <div class="details__rule"></div>
      <h1 class="details__name">Dara Whelby</h1>
      <p class="details__role">Counsellor &amp; Psychotherapist</p>
      <p class="details__quals">BSc (Psychol.), BA, Dip. (Couns. &amp; Psych.)<br>PG.Cert (CBT), FGTrK, ONRE</p>
      <ul class="contact">
        <li><span class="contact__label">M:</span> 555 210 4478</li>
        <li><span class="contact__label">E:</span> dara@willowcrest.com</li>
        <li><span class="contact__label">W:</span> www.willowcrest.com</li>
      </ul>
    </div>
  </section>
</body>
</html>
```